Lumbrix Design

Looking for Lumbrix banner and square design:
Lumbrix Banner
W:1600 px H:400 px
Square
120x120

Logo attached.

Description: Data-Driven stock market portfolio management using quantitative analysis.

```html
<!DOCTYPE html>
<html lang="en">
<head>
<meta charset="utf-8">
<title>Lumbrix Banners</title>
<link rel="stylesheet" href="https://fonts.googleapis.com/css2?family=Montserrat:wght@400;600;700&family=Lato:wght@700&display=swap">
<style>
  :root {
    --page: #ebebeb;
    --navy: #0b2a45;
    --navy-deep: #082238;
    --steel: #3e6282;
    --brand-blue: #0a77c0;
    --white: #ffffff;
    --illus-a: #f3f6fa;
    --illus-b: #fcf2e2;
  }
  html, body {
    margin: 0;
    padding: 0;
    overflow: hidden;
  }
  .canvas {
    position: relative;
    width: 1200px;
    height: 720px;
    background: var(--page);
    overflow: hidden;
  }
  .banner-frame {
    position: absolute;
    left: 67.4px;
    width: 1078px;
    height: 269.5px;
    box-shadow: 0 12px 30px rgba(0, 0, 0, 0.12);
  }
  .banner-frame--wide { top: 41px; }
  .banner-frame--split { top: 376.6px; }
  .banner {
    position: absolute;
    left: 0;
    top: 0;
    width: 1600px;
    height: 400px;
    transform: scale(0.67375);
    transform-origin: 0 0;
    overflow: hidden;
    background: linear-gradient(180deg, var(--navy-deep) 0%, var(--navy) 70%, #123a5c 100%);
    color: var(--white);
  }
  .banner-shapes {
    position: absolute;
    inset: 0;
  }
  .brand {
    position: absolute;
    display: flex;
    align-items: center;
    gap: 18px;
  }
  .brand-dot {
    width: 62px;
    height: 62px;
    border-radius: 50%;
    background: var(--white);
  }
  .brand-name {
    font-family: "Montserrat", sans-serif;
    font-weight: 600;
    font-size: 50px;
    letter-spacing: 1px;
    color: var(--white);
    line-height: 1;
  }
  .headline {
    position: absolute;
    margin: 0;
    font-family: "Montserrat", sans-serif;
    color: var(--white);
    line-height: 1;
  }
  .headline-strong { font-weight: 700; display: block; }
  .headline-light { font-weight: 400; display: block; }
  .tagline {
    position: absolute;
    margin: 0;
    font-family: "Lato", sans-serif;
    font-weight: 700;
    color: var(--white);
  }

  /* Wide banner */
  .banner--wide .brand { left: 628px; top: 30px; }
  .banner--wide .headline { left: 0; width: 1600px; top: 134px; text-align: center; font-size: 50px; }
  .banner--wide .headline-strong { letter-spacing: 1px; }
  .banner--wide .headline-light { margin-top: 26px; letter-spacing: 2px; }
  .banner--wide .tagline { left: 0; width: 1600px; top: 278px; text-align: center; font-size: 27px; line-height: 50px; }

  /* Split banner */
  .banner--split .brand { left: 78px; top: 32px; }
  .banner--split .headline { left: 78px; top: 162px; font-size: 35px; }
  .banner--split .headline-strong { letter-spacing: 1px; }
  .banner--split .headline-light { margin-top: 20px; letter-spacing: 1px; }
  .banner--split .tagline { left: 78px; top: 276px; width: 440px; font-size: 22px; line-height: 40px; }
  .illustration-area {
    position: absolute;
    left: 935px;
    top: 0;
    width: 665px;
    height: 400px;
    background: linear-gradient(135deg, var(--illus-a) 0%, #eef3f9 50%, var(--illus-b) 100%);
  }
</style>
</head>
<body>
<div class="canvas">

  <div class="banner-frame banner-frame--wide">
    <section class="banner banner--wide">
      <svg class="banner-shapes" viewBox="0 0 1600 400" width="1600" height="400" aria-hidden="true">
        <g class="side-panel" fill="var(--steel)" opacity="0.55">
          <path d="M200 0 H330 V400 H200 A200 200 0 0 1 200 0 Z"/>
          <path d="M1400 0 H1270 V400 H1400 A200 200 0 0 0 1400 0 Z"/>
        </g>
      </svg>
      <div class="brand">
        <span class="brand-dot"></span>
        <span class="brand-name">LUMBRIX</span>
      </div>
      <h1 class="headline">
        <span class="headline-strong">EMPOWERING DECISIONS</span>
        <span class="headline-light">THROUGH DATA</span>
      </h1>
      <p class="tagline">Data-Driven stock market portfolio management using<br>quantitative analysis</p>
    </section>
  </div>

  <div class="banner-frame banner-frame--split">
    <section class="banner banner--split">
      <svg class="banner-shapes" viewBox="0 0 1600 400" width="1600" height="400" aria-hidden="true">
        <rect x="930" y="0" width="670" height="400" fill="var(--white)"/>
        <path class="side-panel" fill="var(--brand-blue)" d="M740 0 A190 200 0 0 1 740 400 H620 V0 Z"/>
      </svg>
      <div class="illustration-area" role="img" aria-label="Isometric illustration of analysts working with bar charts, pie charts and financial dashboards"></div>
      <div class="brand">
        <span class="brand-dot"></span>
        <span class="brand-name">LUMBRIX</span>
      </div>
      <h2 class="headline">
        <span class="headline-strong">INSIGHTS THAT DRIVE</span>
        <span class="headline-light">SUCCESS</span>
      </h2>
      <p class="tagline">Data-Driven stock market portfolio management using quantitative analysis</p>
    </section>
  </div>

</div>
</body>
</html>
```